A restaurant needs a new design for menu and presentation flyers.

The name of the restaurant located in Germany is ,, GASTSTÄTTE AM BACH" . It means RESTAURANT THE BROOK. I attached two photos for reference to see the actual fonts.
I would like to have something close to the fonts we have now. I would like to add a crown representation.Any idea is welcomed.

Target Market(s)

GERMANY

Contact Information for Business Card

Must have AM BACH logo.

Requirements
Nice to have
• A crown representation or other symbol who can be representative for our business.
An font close to actual fonts.

```html
<!DOCTYPE html>
<html lang="de">
<head>
<meta charset="utf-8">
<title>Gaststätte Am Bach – Speisekarte</title>
<link rel="stylesheet" href="https://fonts.googleapis.com/css2?family=Arimo:wght@400;700&display=swap">
<style>
  :root {
    --backdrop: #d9d9db;
    --paper: #f8f1e3;
    --paper-light: #fdf9f1;
    --ink: #4a2b23;
    --text: #6a4a3c;
    --gold: #d6bd90;
    --gold-soft: #e6d3ae;
    --sub: #cdb080;
  }
  * { box-sizing: border-box; margin: 0; padding: 0; }
  html, body {
    width: 1200px; height: 1200px; overflow: hidden;
    background: var(--backdrop);
    font-family: "Arimo", Arial, sans-serif;
  }
  .menu {
    position: absolute; left: 190px; top: 20px;
    width: 820px; height: 1160px;
    background: radial-gradient(ellipse at 35% 30%, var(--paper-light), var(--paper) 70%);
    color: var(--text);
  }
  .frame { position: absolute; inset: 0; }
  .ornament {
    position: absolute;
    background: radial-gradient(ellipse, var(--gold-soft), rgba(230,211,174,0) 72%);
  }
  .ornament--top { left: 300px; top: 14px; width: 220px; height: 60px; }
  .ornament--bottom { left: 300px; top: 1086px; width: 220px; height: 60px; }
  .ornament--left { left: 14px; top: 180px; width: 60px; height: 200px; }
  .ornament--right { left: 746px; top: 780px; width: 60px; height: 200px; }

  .brand {
    position: absolute; left: 90px; top: 150px; width: 300px;
    text-align: center;
    font-size: 56px; font-weight: 400; color: var(--ink);
    letter-spacing: 1px;
  }

  .section { position: absolute; }
  .section__title {
    text-align: center; font-size: 14px; font-weight: 700;
    color: var(--ink); text-transform: uppercase; margin-bottom: 8px;
  }
  .item { margin-bottom: 14px; }
  .item__row { display: flex; align-items: baseline; font-size: 14px; }
  .item__leader { flex: 1; border-bottom: 1.5px dotted var(--text); margin: 0 2px; transform: translateY(-3px); }
  .item__sub { font-size: 10px; color: var(--sub); padding-left: 60px; margin-top: 2px; }
  .section--short .item { margin-bottom: 10px; }

  .sec-a { left: 440px; top: 160px; width: 310px; }
  .sec-b { left: 440px; top: 370px; width: 310px; }
  .sec-c { left: 90px; top: 430px; width: 320px; }
  .sec-d { left: 600px; top: 480px; width: 150px; }
  .sec-e { left: 440px; top: 660px; width: 150px; }
  .sec-f { left: 140px; top: 880px; width: 150px; }

  .note {
    position: absolute; left: 430px; top: 880px; width: 330px;
    text-align: center; font-size: 14px; line-height: 1.45; color: var(--text);
  }
</style>
</head>
<body>
<main class="menu">
  <svg class="frame" width="820" height="1160" viewBox="0 0 820 1160" fill="none" stroke="var(--gold)" stroke-width="2">
    <path d="M60 40 H290 M530 40 H760"/>
    <path d="M60 1120 H290 M530 1120 H760"/>
    <path d="M40 60 V170 M40 390 V1100"/>
    <path d="M780 60 V770 M780 990 V1100"/>
  </svg>
  <div class="ornament ornament--top" role="img" aria-label="Goldenes Rankenornament"></div>
  <div class="ornament ornament--bottom" role="img" aria-label="Goldenes Rankenornament"></div>
  <div class="ornament ornament--left" role="img" aria-label="Goldenes Rankenornament"></div>
  <div class="ornament ornament--right" role="img" aria-label="Goldenes Rankenornament"></div>

  <h1 class="brand">Am Bach</h1>

  <section class="section sec-a">
    <h2 class="section__title">Lorem Ipsum</h2>
    <div class="item"><div class="item__row"><span>Lorem Ipsum has been the industry</span><span class="item__leader"></span><span>000</span></div><div class="item__sub">Lorem Ipsum has been the industry</div></div>
    <div class="item"><div class="item__row"><span>Lorem Ipsum has been the industry</span><span class="item__leader"></span><span>000</span></div><div class="item__sub">Lorem Ipsum has been the industry</div></div>
    <div class="item"><div class="item__row"><span>Lorem Ipsum has been the industry</span><span class="item__leader"></span><span>000</span></div><div class="item__sub">Lorem Ipsum has been the industry</div></div>
  </section>

  <section class="section sec-b">
    <h2 class="section__title">Lorem Ipsum</h2>
    <div class="item"><div class="item__row"><span>Lorem Ipsum has been the industry</span><span class="item__leader"></span><span>000</span></div><div class="item__sub">Lorem Ipsum has been the industry</div></div>
    <div class="item"><div class="item__row"><span>Lorem Ipsum has been the industry</span><span class="item__leader"></span><span>000</span></div></div>
  </section>

  <section class="section sec-c">
    <h2 class="section__title">Lorem Ipsum</h2>
    <div class="item"><div class="item__row"><span>Lorem Ipsum has been the industry</span><span class="item__leader"></span><span>000</span></div><div class="item__sub">Lorem Ipsum has been the industry</div></div>
    <div class="item"><div class="item__row"><span>Lorem Ipsum has been the industry</span><span class="item__leader"></span><span>000</span></div><div class="item__sub">Lorem Ipsum has been the industry</div></div>
    <div class="item"><div class="item__row"><span>Lorem Ipsum has been the industry</span><span class="item__leader"></span><span>000</span></div><div class="item__sub">Lorem Ipsum has been the industry</div></div>
    <div class="item"><div class="item__row"><span>Lorem Ipsum has been the industry</span><span class="item__leader"></span><span>000</span></div><div class="item__sub">Lorem Ipsum has been the industry</div></div>
    <div class="item"><div class="item__row"><span>Lorem Ipsum has been the industry</span><span class="item__leader"></span><span>000</span></div><div class="item__sub">Lorem Ipsum has been the industry</div></div>
  </section>

  <section class="section section--short sec-d">
    <h2 class="section__title">Lorem Ipsum</h2>
    <div class="item"><div class="item__row"><span>Lorem Ipsum</span><span class="item__leader"></span><span>000</span></div></div>
    <div class="item"><div class="item__row"><span>Lorem Ipsum</span><span class="item__leader"></span><span>000</span></div></div>
    <div class="item"><div class="item__row"><span>Lorem Ipsum</span><span class="item__leader"></span><span>000</span></div></div>
    <div class="item"><div class="item__row"><span>Lorem Ipsum</span><span class="item__leader"></span><span>000</span></div></div>
    <div class="item"><div class="item__row"><span>Lorem Ipsum</span><span class="item__leader"></span><span>000</span></div></div>
  </section>

  <section class="section section--short sec-e">
    <h2 class="section__title">Lorem Ipsum</h2>
    <div class="item"><div class="item__row"><span>Lorem Ipsum</span><span class="item__leader"></span><span>000</span></div></div>
    <div class="item"><div class="item__row"><span>Lorem Ipsum</span><span class="item__leader"></span><span>000</span></div></div>
    <div class="item"><div class="item__row"><span>Lorem Ipsum</span><span class="item__leader"></span><span>000</span></div></div>
    <div class="item"><div class="item__row"><span>Lorem Ipsum</span><span class="item__leader"></span><span>000</span></div></div>
    <div class="item"><div class="item__row"><span>Lorem Ipsum</span><span class="item__leader"></span><span>000</span></div></div>
  </section>

  <section class="section section--short sec-f">
    <h2 class="section__title">Lorem Ipsum</h2>
    <div class="item"><div class="item__row"><span>Lorem Ipsum</span><span class="item__leader"></span><span>000</span></div></div>
    <div class="item"><div class="item__row"><span>Lorem Ipsum</span><span class="item__leader"></span><span>000</span></div></div>
    <div class="item"><div class="item__row"><span>Lorem Ipsum</span><span class="item__leader"></span><span>000</span></div></div>
    <div class="item"><div class="item__row"><span>Lorem Ipsum</span><span class="item__leader"></span><span>000</span></div></div>
    <div class="item"><div class="item__row"><span>Lorem Ipsum</span><span class="item__leader"></span><span>000</span></div></div>
  </section>

  <p class="note">Lorem Ipsum has been the industry.Lorem Ipsum has been the industry.Lorem Ipsum has been the industry.Lorem Ipsum has been the industry.Lorem Ipsum has been the industry.Lorem Ipsum has been the industry.Lorem Ipsum has been the industry.Lorem Ipsum has been the industry.</p>
</main>
</body>
</html>
```